diesel mechanic business card design

granite diesel is a new and upcoming business we are looking for some bad ass designs to help get us started we offer 24 hour road service, off road recovery, welding and custom fabrications we are diesel mechanics so our design should be bold and eye catching flames wrenches engine parts are cool we work in an industrial environment around heavy trucks and equipment this in not a quick grease we fix it all nothing is to big or to small the colors red and black are always a plus but we are open to anything you guys can come up with ready set go

Target Market(s)

other small business primarily trucking and transportation companys

Industry/Entity Type

Business

Contact Information for Business Card

company name Granitte diesel truck & trailer repair / address 14 rear north halloway ave taylor PA 18503 / ownersAdam DeLuccie 570-555-0143 / Walter Dombrosky 570-555-0178 E mail brentkovalsky@mailbox-example.com fax 570-555-0192

Requirements
Nice to have
• industrial modern design
Should not have
• rainbows butterfly's unicorns or cupcakes

```html
<!DOCTYPE html>
<html lang="en">
<head>
<meta charset="utf-8">
<title>Granitte Diesel Truck &amp; Trailer Repair – Business Card</title>
<link rel="stylesheet" href="https://fonts.googleapis.com/css2?family=Open+Sans:wght@400;600;700;800&display=swap">
<style>
  :root {
    --backdrop: #e6e1d8;
    --card-white: #f4f4f2;
    --band-black: #161616;
    --brand-red: #c1202a;
    --brand-red-dark: #a3161f;
    --text-white: #ffffff;
    --card-shadow: 0 10px 28px rgba(0,0,0,0.28);
  }
  * { box-sizing: border-box; margin: 0; padding: 0; }
  html, body {
    width: 1200px; height: 885px; overflow: hidden;
    background: var(--backdrop);
    font-family: "Open Sans", Arial, sans-serif;
  }
  .stage { position: relative; width: 1200px; height: 885px; }
  .card {
    position: absolute; top: 294px;
    width: 520px; height: 297px;
    border-radius: 4px; overflow: hidden;
    box-shadow: var(--card-shadow);
  }
  /* ---------- Front ---------- */
  .card--front { left: 50px; background: var(--brand-red); display: flex; flex-direction: column; }
  .front__brand {
    height: 128px; background: var(--card-white);
    display: flex; align-items: center; justify-content: center; gap: 16px;
  }
  .brand-art {
    width: 96px; height: 80px; border-radius: 3px;
    background: linear-gradient(135deg, #d9474f, var(--brand-red-dark));
  }
  .brand-name {
    font-weight: 800; text-transform: uppercase; color: var(--brand-red);
    line-height: 1.05;
  }
  .brand-name__main { display: block; font-size: 40px; letter-spacing: 1px; }
  .brand-name__sub { display: block; font-size: 14px; letter-spacing: 1.4px; margin-top: 4px; }
  .owners-wrap {
    background: linear-gradient(180deg, var(--band-black) 0 62px, var(--brand-red) 62px);
  }
  .owners {
    display: flex; justify-content: center; gap: 34px;
    padding: 9px 0 6px;
  }
  .owner { text-align: left; }
  .owner__name {
    display: block; color: var(--brand-red); font-weight: 600; font-size: 19px;
    height: 26px; line-height: 26px;
  }
  .owner__phone {
    display: flex; align-items: center; gap: 6px;
    color: var(--text-white); font-size: 17px; margin-top: 2px;
  }
  .owner__phone svg { width: 13px; height: 13px; flex: none; }
  .owner-divider {
    width: 1px; height: 22px; background: #8a8a8a; align-self: flex-start; margin-top: 2px;
  }
  .front__contact {
    flex: 1; display: flex; flex-direction: column; justify-content: center; align-items: center;
    color: var(--text-white); font-size: 16px; font-weight: 600; line-height: 1.55;
    font-style: normal; padding-bottom: 8px;
    background: linear-gradient(180deg, var(--brand-red) 0%, var(--brand-red-dark) 100%);
  }
  /* ---------- Back ---------- */
  .card--back {
    left: 630px;
    background: linear-gradient(135deg, #d23a43 0%, var(--brand-red) 45%, var(--brand-red-dark) 100%);
    display: flex; align-items: center; justify-content: center; gap: 18px;
  }
  .card--back .brand-art {
    width: 104px; height: 88px;
    background: linear-gradient(135deg, #ffffff, #e9e9e9);
  }
  .card--back .brand-name { color: var(--text-white); }
</style>
</head>
<body>
<main class="stage">

  <section class="card card--front" aria-label="Business card front">
    <div class="front__brand">
      <div class="brand-art" role="img" aria-label="Illustration of a heavy semi truck cab"></div>
      <p class="brand-name">
        <span class="brand-name__main">Granitte</span>
        <span class="brand-name__sub">Diesel Truck &amp; Trailer Repair</span>
      </p>
    </div>
    <div class="owners-wrap">
      <div class="owners">
        <div class="owner">
          <span class="owner__name">Brent Kovalsky</span>
          <span class="owner__phone">
            <svg viewBox="0 0 24 24" aria-hidden="true"><rect width="24" height="24" rx="4" fill="#c1202a"/><path d="M8 5l2.5 4-1.8 1.5c.9 1.9 2.3 3.3 4.2 4.2L14.4 13l4 2.5-1 3c-6.3-.3-10.6-4.6-10.9-10.9z" fill="#fff"/></svg>
            570-555-0143
          </span>
        </div>
        <span class="owner-divider" aria-hidden="true"></span>
        <div class="owner">
          <span class="owner__name">Walter Dombrosky</span>
          <span class="owner__phone">
            <svg viewBox="0 0 24 24" aria-hidden="true"><rect width="24" height="24" rx="4" fill="#c1202a"/><path d="M8 5l2.5 4-1.8 1.5c.9 1.9 2.3 3.3 4.2 4.2L14.4 13l4 2.5-1 3c-6.3-.3-10.6-4.6-10.9-10.9z" fill="#fff"/></svg>
            570-555-0178
          </span>
        </div>
      </div>
    </div>
    <address class="front__contact">
      <span>fax: 570-555-0192</span>
      <span>brentkovalsky@mailbox-example.com</span>
      <span>14 rear north halloway ave ashvale OH 44999</span>
    </address>
  </section>

  <section class="card card--back" aria-label="Business card back">
    <div class="brand-art" role="img" aria-label="Illustration of a heavy semi truck cab"></div>
    <p class="brand-name">
      <span class="brand-name__main">Granitte</span>
      <span class="brand-name__sub">Diesel Truck &amp; Trailer Repair</span>
    </p>
  </section>

</main>
</body>
</html>
```